KDWB Business Card

Looking for a business card design to incorporate our branding. We want to only use the colors listing in the Branding Package (attached).
Updates

Target Market(s)

People who need their phone or device fixed.

Industry/Entity Type

Electronics

Contact Information for Business Card

Please use:

Brightwick Gadget Clinic LLC
4810 E Harlow Ridge Rd
Suite 417
San Antonio, TX 78163

Marcus Delgrove, Store Manager

(210) 555-0147

Requirements
Must have
• Must include the colors that are contained within the Branding Package PDF file.

```html
<!DOCTYPE html>
<html lang="en">
<head>
<meta charset="utf-8">
<title>Brightwick Gadget Clinic – Business Card</title>
<link rel="stylesheet" href="https://fonts.googleapis.com/css2?family=Questrial&display=swap">
<style>
  :root {
    --orange: #e0521c;
    --orange-light: #ea6a2a;
    --card-white: #f4f4f3;
    --grey-text: #5b5b5b;
    --backdrop: #d9d6d1;
  }
  * { box-sizing: border-box; margin: 0; padding: 0; }
  html, body {
    width: 1200px; height: 625px; overflow: hidden;
    background: var(--backdrop);
    font-family: "Questrial", Arial, sans-serif;
  }
  .stage { position: relative; width: 1200px; height: 625px; }
  .card {
    position: absolute; top: 162px;
    width: 520px; height: 300px;
    border-radius: 20px; overflow: hidden;
    background: var(--card-white);
    box-shadow: 0 2px 6px rgba(0,0,0,.18);
  }
  .card--front { left: 50px; }
  .card--back { left: 630px; }

  /* front */
  .front__band {
    position: absolute; left: 0; right: 0; bottom: 0; height: 76px;
    background: linear-gradient(100deg, var(--orange), var(--orange-light));
  }
  .front__company {
    position: absolute; left: 96px; top: 12px;
    color: var(--grey-text); font-size: 14px; white-space: nowrap;
  }
  .front__contact { position: absolute; left: 96px; top: 38px; width: 300px; }
  .name-tab {
    display: flex; align-items: center; gap: 12px;
    height: 32px; padding: 0 14px 0 8px;
    background: var(--orange); color: #fff;
    border-radius: 8px;
    font-size: 19px; width: 232px; white-space: nowrap;
  }
  .name-tab__square {
    width: 20px; height: 20px; border-radius: 4px; background: #fff; flex: none;
  }
  .info-box {
    margin-left: 40px;
    border: 1.5px solid var(--orange); border-top: none;
    border-radius: 0 0 12px 12px;
    padding: 8px 14px 10px;
    color: var(--orange); font-size: 12px; line-height: 1.5;
  }
  .info-box__gap { height: 8px; }

  /* back */
  .back__mark {
    position: absolute; left: 50%; top: 50%;
    transform: translate(-50%, -50%);
    display: flex; align-items: center; gap: 14px;
  }
  .back__square {
    width: 30px; height: 30px; border-radius: 6px; background: var(--orange); flex: none;
  }
  .back__name { color: var(--orange); font-size: 28px; white-space: nowrap; }
</style>
</head>
<body>
<main class="stage">
  <section class="card card--front" aria-label="Card front">
    <p class="front__company">Brightwick Gadget Clinic</p>
    <div class="front__contact">
      <div class="name-tab"><span class="name-tab__square"></span>Marcus Delgrove</div>
      <div class="info-box">
        <p>Store Manager</p>
        <p>(210) 555-0147</p>
        <div class="info-box__gap"></div>
        <p>4810 E Harlow Ridge Rd</p>
        <p>Suite 417</p>
        <p>San Antonio, TX 78163</p>
      </div>
    </div>
    <div class="front__band"></div>
  </section>

  <section class="card card--back" aria-label="Card back">
    <div class="back__mark">
      <span class="back__square"></span>
      <span class="back__name">Brightwick Gadget Clinic</span>
    </div>
  </section>
</main>
</body>
</html>
```